Redesign and move to Wordpress for corvandel.com

Our website needs a redesign and at the same time we are moving it to Wordpress. Please help us with a new digital professional look and feel.

We are an Australian Software Engineering company specialising in advanced software development using in A.I., PLatform Engineering, Integration and Cloud. See the current corvandel.com for more information about us.

```html
<!DOCTYPE html>
<html lang="en">
<head>
<meta charset="utf-8">
<title>corvandel — AI, Cloud and Integration</title>
<link rel="stylesheet" href="https://fonts.googleapis.com/css2?family=Orbitron:wght@500;700;800;900&family=Exo+2:wght@400;500;600&display=swap">
<style>
:root{
  --navy:#061523;
  --teal:#3dbdb8;
  --teal-2:#46c6c2;
  --blue:#1d4f93;
  --ink:#111;
  --grey:#555;
  --mist:#eefafc;
  --slot:#e8e8e8;
  --white:#fff;
}
*{box-sizing:border-box;margin:0;padding:0}
html,body{width:1200px;height:4673px;overflow:hidden}
body{position:relative;background:var(--white);font-family:"Exo 2",sans-serif;color:var(--ink)}
.abs{position:absolute}
.display{font-family:"Orbitron",sans-serif;font-weight:800;letter-spacing:1px;text-transform:uppercase}
.center{left:0;width:1200px;text-align:center}
.btn{position:absolute;display:flex;align-items:center;justify-content:center;gap:10px;font-family:"Orbitron",sans-serif;font-weight:700;font-size:14px;letter-spacing:1px;text-transform:uppercase;color:var(--white)}
.btn svg{width:13px;height:13px}
.sec-mark{position:absolute;left:585px;width:30px;height:30px;border:3px solid #222}
.sec-mark.light{border-color:var(--white)}

/* hero */
.hero{left:0;top:0;width:1200px;height:600px;background:linear-gradient(100deg,#051320 0%,#07243a 55%,#0b3550 100%);clip-path:polygon(0 0,1200px 0,1200px 600px,0 490px)}
.hero-art{left:640px;top:90px;width:560px;height:500px;background:radial-gradient(ellipse at 45% 40%,rgba(90,200,255,.55),rgba(30,110,180,.25) 45%,transparent 70%)}
.hero-accent{left:0;top:0;width:1200px;height:600px;background:var(--teal);clip-path:polygon(820px 560px,1200px 580px,1200px 600px)}
.logo{display:flex;align-items:center;gap:14px;font-family:"Exo 2",sans-serif;font-weight:500;font-size:34px;color:var(--white);letter-spacing:1px}
.logo i{display:block;width:44px;height:44px;border:3px solid currentColor}
.nav{display:flex;gap:42px;font-family:"Orbitron",sans-serif;font-weight:500;font-size:13px;color:var(--white);text-transform:uppercase}
.nav .on{text-decoration:underline;text-underline-offset:4px}
.hero h1{left:112px;top:122px;width:560px;font-size:46px;line-height:54px;color:var(--white)}
.hero h1 span{color:var(--teal-2)}

/* about */
.section-title{font-size:44px}
.section-title span{color:var(--teal)}
.about-copy{left:240px;top:806px;width:720px;text-align:center;font-size:14px;line-height:25px;color:var(--grey)}
.partners{left:200px;top:1050px;width:800px;display:flex;justify-content:space-between;align-items:center}
.partner{width:180px;height:110px;display:flex;align-items:center;justify-content:center;font-family:"Exo 2",sans-serif;font-weight:600;font-size:28px;color:#333}
.partner.featured{background:var(--white);box-shadow:0 4px 18px rgba(0,0,0,.12)}

/* services */
.services{left:0;top:1260px;width:1200px;height:760px;background:linear-gradient(180deg,#3cb3b6 0%,#2a86ad 45%,#1d4f93 100%);clip-path:polygon(0 10px,1200px 100px,1200px 700px,0 753px)}
.services-stripe{left:0;top:1262px;width:770px;height:12px;background:var(--blue);clip-path:polygon(0 0,770px 0,770px 12px,0 6px)}
.svc-card{position:absolute;width:290px;color:var(--white)}
.svc-card.active{background:rgba(255,255,255,.12)}
.svc-head{display:flex;align-items:center;gap:18px;font-family:"Orbitron",sans-serif;font-weight:700;font-size:13px;line-height:20px;text-transform:uppercase}
.svc-icon{width:50px;height:50px;flex:none;border-radius:8px;background:var(--blue);display:flex;align-items:center;justify-content:center}
.svc-icon svg{width:28px;height:28px}
.svc-card p{margin-top:14px;font-size:13.5px;line-height:21px;color:#e6f3f7}

/* news */
.arrow-dot{width:22px;height:22px}
.article{position:absolute;top:2316px;width:312px}
.article .thumb{height:224px}
.article h3{margin-top:26px;font-family:"Orbitron",sans-serif;font-weight:700;font-size:13.5px;color:var(--ink)}
.article p{margin-top:10px;font-size:12.5px;line-height:19px;color:#555}
.article .more{margin-top:18px;display:flex;align-items:center;gap:9px;font-family:"Orbitron",sans-serif;font-weight:700;font-size:13px;color:var(--blue)}
.article .more svg{width:12px;height:12px}

/* booking */
.booking-bg{left:0;top:2793px;width:1200px;height:1100px;background:var(--mist)}
.cal-card{left:112px;top:3120px;width:488px;height:574px;background:var(--white);box-shadow:0 6px 24px rgba(0,0,0,.08)}
.cal-photo{left:127px;top:3134px;width:457px;height:200px;background:linear-gradient(135deg,#3a3a3a,#6c5a4d 50%,#2a2a2a)}
.cta-pill{left:196px;top:3305px;width:319px;height:58px;background:var(--blue);border-radius:10px 10px 0 0;color:var(--white);font-family:"Orbitron",sans-serif;font-weight:700;font-size:19px;display:flex;align-items:center;justify-content:center;letter-spacing:1px}
.month{left:112px;top:3388px;width:488px;display:flex;justify-content:center;gap:70px;font-family:"Orbitron",sans-serif;font-weight:700;font-size:20px}
.dow{position:absolute;top:3438px;width:50px;margin-left:-25px;text-align:center;font-family:"Orbitron",sans-serif;font-weight:600;font-size:11px}
.day{position:absolute;width:26px;height:26px;margin:-13px 0 0 -13px;border-radius:50%;background:#e4e4e4;font-family:"Orbitron",sans-serif;font-weight:600;font-size:9px;display:flex;align-items:center;justify-content:center}
.day.sel{background:var(--blue);color:var(--white)}
.book-panel{left:625px;top:3120px;width:463px;height:574px;background:var(--white)}
.panel-title{position:absolute;left:625px;width:463px;text-align:center;font-family:"Orbitron",sans-serif;font-weight:700;font-size:18px;color:var(--blue)}
.slot{position:absolute;left:674px;width:341px;height:55px;background:var(--slot);display:flex;align-items:center;justify-content:center;font-family:"Orbitron",sans-serif;font-size:14px;color:#444}

/* footer */
.footer{left:0;top:3840px;width:1200px;height:833px;background:var(--navy);clip-path:polygon(0 40px,1200px 0,1200px 833px,0 833px)}
.promo{left:112px;top:3793px;width:976px;height:488px;background:linear-gradient(105deg,#1c4f93 0%,#2a7aa8 55%,#3dbdb8 100%)}
.promo-title{left:112px;width:976px;top:3904px;text-align:center;font-size:42px;line-height:54px;color:var(--white)}
.email{left:176px;top:4125px;width:848px;height:93px;background:var(--white);display:flex;align-items:center;justify-content:space-between;padding:0 52px}
.email span{font-family:"Orbitron",sans-serif;font-size:20px;letter-spacing:4px;color:#555}
.social{width:44px;height:44px;border-radius:50%;background:var(--white)}
</style>
</head>
<body>

<!-- Hero -->
<section class="abs hero">
  <div class="abs hero-art" role="img" aria-label="Glowing digital brain hovering above an open hand"></div>
  <div class="abs logo" style="left:110px;top:24px"><i></i>corvandel</div>
  <nav class="abs nav" style="left:543px;top:41px">
    <span class="on">Home</span><span>About Us</span><span>Services</span><span>Blog</span><span>Contact</span>
    <svg width="14" height="14" viewBox="0 0 14 14" fill="none" stroke="#fff" stroke-width="2"><circle cx="6" cy="6" r="4.5"/><path d="M9.5 9.5 13 13"/></svg>
  </nav>
  <h1 class="abs display"><span>Innovating with AI, Cloud, and</span> Integration for Future-Ready</h1>
  <div class="btn" style="left:112px;top:370px;width:174px;height:44px;background:var(--teal)">Get Started
    <svg viewBox="0 0 12 12"><circle cx="6" cy="6" r="6" fill="#fff"/><path d="M5 3.5 7.5 6 5 8.5" stroke="#3dbdb8" stroke-width="1.6" fill="none"/></svg></div>
</section>
<div class="abs hero-accent"></div>

<!-- About -->
<div class="sec-mark" style="top:675px"></div>
<h2 class="abs display section-title center" style="top:712px">About <span>Us</span></h2>
<p class="abs about-copy">At corvandel, we craft bespoke software solutions that are not available on the market. By building organizations market-leading products, process automation, legacy system enablement, or advanced intelligent systems, we empower our customers to achieve a competitive edge in their industry.</p>
<div class="btn" style="left:513px;top:927px;width:174px;height:45px;background:var(--blue)">Learn More
  <svg viewBox="0 0 12 12"><circle cx="6" cy="6" r="6" fill="#fff"/><path d="M5 3.5 7.5 6 5 8.5" stroke="#1d4f93" stroke-width="1.6" fill="none"/></svg></div>
<div class="abs partners">
  <div class="partner">Normaq</div>
  <div class="partner">Halvex</div>
  <div class="partner featured">Tarvik</div>
  <div class="partner" style="font-size:22px">Brightfund</div>
</div>

<!-- Services -->
<section class="abs services"></section>
<div class="abs services-stripe"></div>
<div class="sec-mark light" style="top:1413px"></div>
<h2 class="abs display section-title center" style="top:1452px;color:#fff">Our Services</h2>

<div class="svc-card" style="left:145px;top:1548px">
  <div class="svc-head"><div class="svc-icon"><svg viewBox="0 0 28 28" fill="none" stroke="#fff" stroke-width="1.6"><circle cx="6" cy="8" r="2"/><circle cx="14" cy="8" r="2"/><circle cx="22" cy="8" r="2"/><circle cx="6" cy="20" r="2"/><circle cx="14" cy="20" r="2"/><circle cx="22" cy="20" r="2"/></svg></div>Enterprise Systems<br>Integration</div>
  <p>Automate your business processes internally or externally to improve data quality and process efficiency</p>
</div>
<div class="svc-card active" style="left:444px;top:1532px;width:326px;height:172px;padding:16px 0 0 31px">
  <div class="svc-head"><div class="svc-icon" style="background:var(--teal)"><svg viewBox="0 0 28 28" fill="none" stroke="#fff" stroke-width="1.6"><circle cx="14" cy="14" r="4"/><circle cx="5" cy="5" r="2"/><circle cx="23" cy="5" r="2"/><circle cx="5" cy="23" r="2"/><circle cx="23" cy="23" r="2"/><path d="M7 7l4 4M21 7l-4 4M7 21l4-4M21 21l-4-4"/></svg></div>Micro<br>Services</div>
  <p style="width:270px">Leverage Microservices Architecture to enable quick deployment, dynamically scalable service performance, team...</p>
</div>
<div class="svc-card" style="left:796px;top:1548px">
  <div class="svc-head"><div class="svc-icon"><svg viewBox="0 0 28 28" fill="none" stroke="#fff" stroke-width="1.6"><path d="M8 20h13a5 5 0 0 0 0-10 7 7 0 0 0-13 1 4.5 4.5 0 0 0 0 9z"/><path d="M14 12v6M11 15h6"/></svg></div>Platform<br>Engineering</div>
  <p>For organisations looking to manage the security and cost risks around their cloud infrastructure management</p>
</div>
<div class="svc-card" style="left:145px;top:1746px">
  <div class="svc-head"><div class="svc-icon"><svg viewBox="0 0 28 28" fill="none" stroke="#fff" stroke-width="1.6"><path d="M5 6h18v12H12l-5 4v-4H5z"/><path d="M10 12h8"/></svg></div>Conversational<br>AI</div>
  <p>Enabling legacy systems with conversational user interfaces, or simply building intelligent natural language based services, conversational</p>
</div>
<div class="svc-card" style="left:475px;top:1746px">
  <div class="svc-head"><div class="svc-icon"><svg viewBox="0 0 28 28" fill="none" stroke="#fff" stroke-width="1.6"><rect x="7" y="9" width="14" height="11" rx="3"/><path d="M14 5v4M11 14h.5M17 14h.5"/></svg></div>Copilot /<br>AI Agents</div>
  <p>Automate your business processes internally or externally to improve data quality and process efficiency</p>
</div>
<div class="svc-card" style="left:796px;top:1746px">
  <div class="svc-head"><div class="svc-icon"><svg viewBox="0 0 28 28" fill="none" stroke="#fff" stroke-width="1.6"><rect x="4" y="5" width="9" height="6"/><rect x="15" y="17" width="9" height="6"/><path d="M13 8h5v9M10 11v9h5"/></svg></div>Real-Time Data Stream<br>Processing</div>
  <p>Being able to react to changing business conditions in a precise intelligent way is becoming increasingly important</p>
</div>
<div class="btn" style="left:513px;top:1920px;width:174px;height:46px;border:2px solid #fff">Learn More
  <svg viewBox="0 0 12 12"><circle cx="6" cy="6" r="6" fill="#fff"/><path d="M5 3.5 7.5 6 5 8.5" stroke="#1d4f93" stroke-width="1.6" fill="none"/></svg></div>

<!-- News -->
<div class="sec-mark" style="top:2175px"></div>
<h2 class="abs display section-title center" style="top:2212px">News &amp; <span>Articles</span></h2>
<div class="abs" style="left:548px;top:2268px;width:104px;height:3px;background:var(--blue)"></div>
<svg class="abs arrow-dot" style="left:61px;top:2423px" viewBox="0 0 22 22"><circle cx="11" cy="11" r="11" fill="#3dbdb8"/><path d="M13 6 8 11l5 5" stroke="#fff" stroke-width="2.2" fill="none"/></svg>
<svg class="abs arrow-dot" style="left:1115px;top:2423px" viewBox="0 0 22 22"><circle cx="11" cy="11" r="11" fill="#1d4f93"/><path d="M9 6l5 5-5 5" stroke="#fff" stroke-width="2.2" fill="none"/></svg>

<article class="article" style="left:107px">
  <div class="thumb" role="img" aria-label="Hands typing on a laptop beside a robotic arm" style="background:linear-gradient(135deg,#0f2b3c,#2f7f96 55%,#122433)"></div>
  <h3>AI in SOFTWARE ENGINEERING</h3>
  <p>[Codewright Blog] Codewright Assist is widely known for its code generation feature. Learn how the AI assistant's abilities can extend beyond just code generation.</p>
  <div class="more">Learn More <svg viewBox="0 0 12 12"><circle cx="6" cy="6" r="6" fill="#1d4f93"/><path d="M5 3.5 7.5 6 5 8.5" stroke="#fff" stroke-width="1.6" fill="none"/></svg></div>
</article>
<article class="article" style="left:444px">
  <div class="thumb" role="img" aria-label="Glowing blue digital gear of data particles" style="background:radial-gradient(circle at 50% 55%,#3aa9e8,#0d3d78 50%,#06122a)"></div>
  <h3>INDUSTRY RESEARCH</h3>
  <p>[Halvex Labs] Large language models (LLMs) have transformed many tasks, but prompt engineering remains a challenge. Enter PromptKit: an open-source tool that streamlines</p>
  <div class="more">Learn More <svg viewBox="0 0 12 12"><circle cx="6" cy="6" r="6" fill="#1d4f93"/><path d="M5 3.5 7.5 6 5 8.5" stroke="#fff" stroke-width="1.6" fill="none"/></svg></div>
</article>
<article class="article" style="left:783px">
  <div class="thumb" role="img" aria-label="Small white robot standing on a glowing digital platform" style="background:radial-gradient(circle at 50% 45%,#9fb7c8,#1f4a66 55%,#0a1a26)"></div>
  <h3>Artificial intelligence</h3>
  <p>[Halvex Labs] Halvex Labs discusses prompting strategies that demonstrate how a general language model can perform as a specialist on a medical challenge problem</p>
  <div class="more">Learn More <svg viewBox="0 0 12 12"><circle cx="6" cy="6" r="6" fill="#1d4f93"/><path d="M5 3.5 7.5 6 5 8.5" stroke="#fff" stroke-width="1.6" fill="none"/></svg></div>
</article>

<!-- Booking -->
<div class="abs booking-bg"></div>
<div class="sec-mark" style="top:2975px"></div>
<h2 class="abs display section-title center" style="top:3014px">Book an <span>Obligation</span></h2>
<div class="abs" style="left:572px;top:3070px;width:56px;height:3px;background:var(--blue)"></div>

<div class="abs cal-card"></div>
<div class="abs cal-photo" role="img" aria-label="Portrait photo of the company CTO"></div>
<div class="abs cta-pill">MEET WITH OUR CTO</div>
<div class="abs month"><span>‹</span><span>JAN 2025</span><span>›</span></div>
<div class="dow" style="left:163px">MON</div><div class="dow" style="left:227px">TUE</div><div class="dow" style="left:290px">WED</div><div class="dow" style="left:355px">THU</div><div class="dow" style="left:419px">FRI</div><div class="dow" style="left:482px">SAT</div><div class="dow" style="left:547px">SUN</div>

<div class="day" style="left:290px;top:3485px">1</div><div class="day" style="left:355px;top:3485px">2</div><div class="day" style="left:419px;top:3485px">3</div><div class="day" style="left:482px;top:3485px">4</div><div class="day" style="left:547px;top:3485px">5</div>
<div class="day" style="left:163px;top:3526px">6</div><div class="day" style="left:227px;top:3526px">7</div><div class="day" style="left:290px;top:3526px">8</div><div class="day" style="left:355px;top:3526px">9</div><div class="day" style="left:419px;top:3526px">10</div><div class="day" style="left:482px;top:3526px">11</div><div class="day" style="left:547px;top:3526px">12</div>
<div class="day" style="left:163px;top:3567px">13</div><div class="day" style="left:227px;top:3567px">14</div><div class="day" style="left:290px;top:3567px">15</div><div class="day" style="left:355px;top:3567px">16</div><div class="day" style="left:419px;top:3567px">17</div><div class="day" style="left:482px;top:3567px">18</div><div class="day" style="left:547px;top:3567px">19</div>
<div class="day" style="left:163px;top:3607px">20</div><div class="day" style="left:227px;top:3607px">21</div><div class="day" style="left:290px;top:3607px">22</div><div class="day sel" style="left:355px;top:3607px">23</div><div class="day" style="left:419px;top:3607px">24</div><div class="day" style="left:482px;top:3607px">25</div><div class="day" style="left:547px;top:3607px">26</div>
<div class="day" style="left:163px;top:3648px">27</div><div class="day" style="left:227px;top:3648px">28</div><div class="day" style="left:290px;top:3648px">29</div><div class="day" style="left:355px;top:3648px">30</div><div class="day" style="left:419px;top:3648px">31</div>

<div class="abs book-panel"></div>
<div class="panel-title" style="top:3166px">MEETING DURATION</div>
<div class="slot" style="left:653px;top:3221px;width:404px;height:62px;font-size:17px">30 minutes</div>
<div class="panel-title" style="top:3313px">WHAT TIME WORKS BEST?</div>
<div class="abs" style="left:625px;top:3356px;width:463px;text-align:center;font-size:13px;color:#444">Showing times for 15 January 2025</div>
<div class="abs" style="left:625px;top:3396px;width:463px;text-align:center;font-size:14px;color:var(--blue)">UTC +05:30 New Delhi, Mumbai, Calcutta ⌄</div>
<div class="slot" style="top:3442px">3:30</div>
<div class="slot" style="top:3506px">3:45</div>
<div class="slot" style="top:3570px">4:00</div>

<!-- Footer -->
<footer class="abs footer"></footer>
<div class="abs promo"></div>
<div class="sec-mark light" style="top:3860px"></div>
<h2 class="abs display promo-title">Australia's Largest Health<br>Charity Implements<br>corvandel API MSG Bus</h2>
<div class="abs" style="left:548px;top:4082px;width:104px;height:3px;background:#fff"></div>
<div class="abs email"><span>ENTER EMAIL ADDRESS</span>
  <svg width="28" height="28" viewBox="0 0 28 28"><circle cx="14" cy="14" r="14" fill="#1d4f93"/><path d="M12 8l6 6-6 6" stroke="#fff" stroke-width="2.6" fill="none"/></svg></div>

<div class="abs logo" style="left:470px;top:4368px"><i></i>corvandel</div>
<nav class="abs nav" style="left:327px;top:4460px;width:546px;justify-content:space-between">
  <span>Home</span><span>About Us</span><span>Services</span><span>Blog</span><span>Contact</span>
  <svg width="14" height="14" viewBox="0 0 14 14" fill="none" stroke="#fff" stroke-width="2"><circle cx="6" cy="6" r="4.5"/><path d="M9.5 9.5 13 13"/></svg>
</nav>
<div class="abs" style="left:531px;top:4520px;display:flex;gap:5px">
  <div class="social" aria-label="Social link"></div><div class="social" aria-label="Social link"></div><div class="social" aria-label="Social link"></div>
</div>
<div class="abs center" style="top:4596px;font-size:13px;color:#fff">Copyright@2025 - All Rights Reserved</div>

</body>
</html>
```